Web Design

We need a website for a company based in Doha Qatar called
Lumara Maid Service.

It is the number one maid cleaning service company, and we have branches all over qatar.

Luxury Cleaning Service Provider.

The color scheme is gold, yellow and black like the logo.

Before they get to the website, there is an intro video.

The website should depict luxury.

Target Market(s)

People who need maids at their houses.

Industry/Entity Type

Cleaning Service

Requirements
Must have
• Luxury, Sleek, Modern

The opening sequence is a video which I already have. Its too big to upload here so I am going to put it on youtube.

After the opening sequence, the home page should have a widescreen photo background and it should change every five seconds, the first background photo should be of qatar westbay skyline. Then the second background should be of maid photos in cleaning positions. Then the third background should be of cleaner photos etc.

We will send you all the tabs and all the content later.

```html
<!DOCTYPE html>
<html lang="en">
<head>
<meta charset="utf-8">
<title>Lumara Maid Service</title>
<link rel="stylesheet" href="https://fonts.googleapis.com/css2?family=Open+Sans:wght@300;400&family=Roboto:wght@400&display=swap">
<style>
  :root {
    --header-bg: #f4f4f4;
    --nav-text: #2e2e2e;
    --title-brown: #5a2f0e;
    --brand-gold: #b8860b;
    --sky-top: #e4e7ea;
    --sky-mid: #d8dde2;
    --water: #cfd4d8;
    --player-bar: rgba(35, 35, 35, 0.9);
    --accent-red: #e0444f;
    --track: #5a5a5a;
    --control-light: #e6e6e6;
    --gold-light: #f2cf63;
    --gold-dark: #c9a010;
    --footer-bg: #333333;
    --footer-text: #f0f0f0;
    --icon-circle: #e8e8e8;
  }
  * { box-sizing: border-box; margin: 0; padding: 0; }
  html, body { width: 1200px; height: 846px; overflow: hidden; }
  body { position: relative; font-family: "Roboto", sans-serif; background: var(--sky-mid); }

  .site-header {
    position: absolute; left: 0; top: 0; width: 1200px; height: 115px;
    background: var(--header-bg);
    box-shadow: 0 2px 6px rgba(0,0,0,0.18);
    z-index: 2;
  }
  .brand {
    position: absolute; left: 174px; top: 40px;
    display: flex; align-items: center; gap: 10px;
    font-family: "Open Sans", sans-serif; font-weight: 400;
    font-size: 20px; color: var(--brand-gold); letter-spacing: 0.5px;
  }
  .brand-dot { width: 26px; height: 26px; border-radius: 50%; background: var(--gold-light); }
  .main-nav { position: absolute; top: 56px; left: 628px; display: flex; }
  .main-nav a {
    font-size: 16px; color: var(--nav-text); text-decoration: none; margin-right: 27px;
  }
  .main-nav a:last-child { margin-left: 7px; margin-right: 0; }

  .hero {
    position: absolute; left: 0; top: 115px; width: 1200px; height: 620px;
    background: linear-gradient(180deg, var(--sky-top) 0%, var(--sky-mid) 55%, #c9cfd3 64%, var(--water) 100%);
  }
  .hero-title {
    position: absolute; left: 0; width: 1137px; top: 30px; text-align: center;
    font-family: "Open Sans", sans-serif; font-weight: 400; font-size: 37px;
    color: var(--title-brown); letter-spacing: 0.5px;
  }
  .video-player {
    position: absolute; left: 247px; top: 98px; width: 703px; height: 410px;
    border-radius: 6px; overflow: hidden; border: 1px solid #9a9a9a;
  }
  .video-frame {
    width: 100%; height: 100%;
    background: linear-gradient(120deg, #e6c7a4 0%, #d9b48a 40%, #c7d4ea 70%, #dfc3a0 100%);
  }
  .video-controls {
    position: absolute; left: 0; bottom: 0; width: 100%; height: 62px;
    background: var(--player-bar);
  }
  .time {
    position: absolute; left: 506px; top: 21px; font-family: "Roboto", sans-serif;
    font-size: 16px; color: var(--control-light);
  }
  .cta {
    position: absolute; left: 487px; top: 534px; width: 244px; height: 62px;
    background: linear-gradient(180deg, var(--gold-light) 0%, var(--gold-dark) 100%);
    border-radius: 2px; color: #fff; text-decoration: none;
    font-family: "Open Sans", sans-serif; font-weight: 300; font-size: 33px;
    display: flex; align-items: center; justify-content: center;
  }

  .site-footer {
    position: absolute; left: 0; top: 735px; width: 1200px; height: 111px;
    background: var(--footer-bg); color: var(--footer-text); font-size: 14px;
  }
  .copyright { position: absolute; left: 172px; top: 52px; }
  .social { position: absolute; left: 556px; top: 44px; display: flex; gap: 5px; }
  .social span { width: 32px; height: 32px; border-radius: 50%; background: var(--icon-circle); display: block; }
  .legal { position: absolute; right: 171px; top: 50px; }
</style>
</head>
<body>
  <header class="site-header">
    <div class="brand"><span class="brand-dot"></span>Lumara Maid Service</div>
    <nav class="main-nav">
      <a href="#">Home</a><a href="#">About Us</a><a href="#">Services</a><a href="#">Products</a><a href="#">Contact</a>
    </nav>
  </header>

  <main class="hero" role="img" aria-label="West Bay skyline of Doha over the water, soft faded background photo">
    <h1 class="hero-title">LUMARA MAID SERVICE</h1>

    <div class="video-player">
      <div class="video-frame" role="img" aria-label="Intro video still: a smiling maid in a kitchen giving a thumbs up"></div>
      <div class="video-controls">
        <svg width="703" height="62" viewBox="0 0 703 62" style="position:absolute;left:0;top:0">
          <circle cx="37" cy="31" r="13" fill="none" stroke="var(--control-light)" stroke-width="2.5"/>
          <path d="M33 24 L43 31 L33 38 Z" fill="var(--control-light)"/>
          <path d="M74 27 h5 l6 -5 v18 l-6 -5 h-5 z" fill="var(--accent-red)"/>
          <path d="M88 26 q4 5 0 10 M91 23 q7 8 0 16" fill="none" stroke="var(--accent-red)" stroke-width="2"/>
          <g fill="var(--accent-red)">
            <rect x="105" y="24" width="3" height="14"/><rect x="111" y="24" width="3" height="14"/>
            <rect x="117" y="24" width="3" height="14"/><rect x="123" y="24" width="3" height="14"/>
            <rect x="129" y="24" width="3" height="14"/>
          </g>
          <g fill="var(--track)">
            <rect x="135" y="24" width="3" height="14"/><rect x="141" y="24" width="3" height="14"/>
          </g>
          <rect x="177" y="29" width="306" height="5" rx="2.5" fill="var(--track)"/>
          <rect x="177" y="29" width="108" height="5" rx="2.5" fill="var(--accent-red)"/>
          <rect x="620" y="24" width="18" height="14" fill="none" stroke="var(--control-light)" stroke-width="3"/>
          <circle cx="671" cy="31" r="6" fill="none" stroke="var(--control-light)" stroke-width="4" stroke-dasharray="3 2"/>
          <circle cx="671" cy="31" r="5" fill="none" stroke="var(--control-light)" stroke-width="2"/>
        </svg>
        <span class="time">01:30 / 04:55</span>
      </div>
    </div>

    <a class="cta" href="#">GET START</a>
  </main>

  <footer class="site-footer">
    <p class="copyright">Copy right © 2014 All Rights</p>
    <div class="social">
      <span aria-label="Social link 1"></span><span aria-label="Social link 2"></span><span aria-label="Social link 3"></span>
    </div>
    <p class="legal">Privacy policy / Contact us</p>
  </footer>
</body>
</html>
```